IT Support Business needs a Flyer Designed

Have just had new logo and business cards made for new business called Byte Harbor, am now in need of a new flyer design. Byte Harbor will be providing home and small business it support.
Updates
Byte Harbor flyer design brief has been uploaded. The contest has also been changed to payment guaranteed.
If you need anymore information please feel free to contact myself.
Project Deadline Extended
Reason: I signed up early to take advantage of the artfolly 24 hour sale, and was a few days late in providing a design brief. Therefore I am extending the deadline by 2 days, to ensure it lasts for a good 2 weeks.
Have worked on and refined the Design Brief a bit more, hoping it makes it a bit clearer as to what I want on the flyer. If you have any questions please do not hesitate to ask.
I have refined the design brief overnight, after receiving some feedback, please refer to newly uploaded file for this morning. I am hoping it makes things clearer and easier.
Industry/Entity Type
Small Business

```html
<!DOCTYPE html>
<html lang="en">
<head>
<meta charset="utf-8">
<title>Byte Harbor – Computer Repair Flyer</title>
<link rel="stylesheet" href="https://fonts.googleapis.com/css2?family=Bitter:wght@400&family=Open+Sans:wght@400;600&display=swap">
<style>
  :root {
    --brand-red: #e8392a;
    --brand-blue: #1c6aae;
    --label-blue: #2a6fae;
    --ink: #2e2e2e;
    --paper: #ffffff;
    --rule: #dcdcdc;
    --photo-light: #f2f2f2;
    --photo-mid: #bdbdbd;
    --photo-dark: #6d6d6d;
  }
  * { margin: 0; padding: 0; box-sizing: border-box; }
  html, body { width: 1200px; height: 798px; overflow: hidden; background: var(--paper); }
  .flyer {
    position: relative;
    width: 1200px;
    height: 798px;
    background: var(--paper);
    font-family: "Open Sans", Arial, sans-serif;
    overflow: hidden;
  }
  .swoosh { position: absolute; inset: 0; width: 1200px; height: 798px; }
  .hero-photo {
    position: absolute;
    left: 39px; top: 74px;
    width: 1118px; height: 223px;
    background: linear-gradient(100deg, var(--photo-dark) 0%, var(--photo-mid) 35%, var(--photo-light) 75%, var(--paper) 100%);
  }
  .logo-panel {
    position: absolute;
    left: 700px; top: 0;
    width: 500px; height: 144px;
    background: var(--paper);
    border-bottom-left-radius: 44px;
  }
  .brand {
    position: absolute;
    left: 770px; top: 62px;
    display: flex; align-items: center; gap: 14px;
  }
  .brand-dot { width: 34px; height: 34px; border-radius: 50%; background: var(--brand-red); }
  .brand-name {
    font-family: "Open Sans", Arial, sans-serif;
    font-weight: 600;
    font-size: 44px;
    color: var(--brand-blue);
    letter-spacing: 1px;
    line-height: 1;
  }
  .headline {
    position: absolute;
    left: 0; right: 0; top: 332px;
    text-align: center;
    font-family: "Bitter", Georgia, serif;
    font-weight: 400;
    font-size: 57px;
    color: var(--ink);
    line-height: 1;
  }
  .services {
    position: absolute;
    left: 29px; top: 444px;
    display: flex;
    list-style: none;
  }
  .service {
    width: 144px;
    display: flex; flex-direction: column; align-items: center;
    text-align: center;
  }
  .service svg { width: 72px; height: 72px; fill: var(--brand-red); }
  .service-label {
    margin-top: 18px;
    font-size: 16.5px;
    line-height: 1.18;
    color: var(--label-blue);
  }
  .rule { position: absolute; left: 60px; width: 1080px; height: 1px; background: var(--rule); }
  .rule-top { top: 645px; }
  .rule-bottom { top: 772px; }
  .pricing {
    position: absolute;
    left: 0; right: 0; top: 654px;
    text-align: center;
    font-size: 22px;
    line-height: 34px;
    color: var(--brand-red);
  }
</style>
</head>
<body>
<main class="flyer">
  <div class="hero-photo" role="img" aria-label="Black and white photo of a hand typing on a computer keyboard"></div>
  <div class="logo-panel"></div>

  <svg class="swoosh" viewBox="0 0 1200 798" aria-hidden="true">
    <path d="M0,0 H330 C200,18 80,70 0,150 Z" fill="var(--brand-red)"/>
    <path d="M0,168 C80,85 210,30 360,0 H380 C230,34 95,100 0,190 Z" fill="var(--brand-blue)"/>
    <path d="M1200,600 C1150,690 1040,760 940,798 H1200 Z" fill="var(--brand-blue)"/>
    <path d="M1200,575 C1140,680 1020,750 880,785 C1030,740 1150,665 1200,598 Z" fill="var(--brand-red)"/>
  </svg>

  <div class="brand">
    <span class="brand-dot"></span>
    <span class="brand-name">Byte Harbor</span>
  </div>

  <h1 class="headline">Computer Repair You Can Depend On</h1>

  <ul class="services">
    <li class="service">
      <svg viewBox="0 0 72 72"><path d="M10,8 h52 v40 h-4 v-36 h-44 v36 h-4 z M4,50 h64 v6 h-64 z"/><path d="M26,20 l12,12 l-4,4 l-12,-12 z M40,18 a8,8 0 1 1 8,14 l-4,-4 z"/></svg>
      <span class="service-label">Computer Repair, Service, Install And Upgrade</span>
    </li>
    <li class="service">
      <svg viewBox="0 0 72 72"><rect x="24" y="4" width="24" height="16" rx="2"/><rect x="34" y="20" width="4" height="12"/><rect x="10" y="30" width="52" height="4"/><rect x="10" y="30" width="4" height="12"/><rect x="34" y="30" width="4" height="12"/><rect x="58" y="30" width="4" height="12"/><circle cx="12" cy="52" r="10"/><circle cx="36" cy="52" r="10"/><circle cx="60" cy="52" r="10"/></svg>
      <span class="service-label">Setting Up Secure Networks</span>
    </li>
    <li class="service">
      <svg viewBox="0 0 72 72"><path d="M8,6 h56 v50 h-56 z M13,11 v40 h46 v-40 z"/><path d="M32,26 a3,3 0 0 1 6,0 v14 l10,3 v16 h-20 l-8,-12 l4,-2 l8,6 z"/></svg>
      <span class="service-label">Setting up New Hardware</span>
    </li>
    <li class="service">
      <svg viewBox="0 0 72 72"><rect x="4" y="10" width="8" height="8"/><rect x="14" y="10" width="8" height="8"/><rect x="24" y="10" width="8" height="8"/><rect x="34" y="10" width="8" height="8"/><rect x="44" y="10" width="8" height="8"/><rect x="54" y="10" width="8" height="8"/><rect x="64" y="10" width="6" height="8"/><path d="M38,26 l20,20 l-9,1 l6,12 l-4,2 l-6,-12 l-7,6 z"/></svg>
      <span class="service-label">Software Install And Configuration</span>
    </li>
    <li class="service">
      <svg viewBox="0 0 72 72"><path d="M36,14 a16,16 0 0 1 10,28 v8 h-20 v-8 a16,16 0 0 1 10,-28 z"/><rect x="28" y="53" width="16" height="4"/><rect x="30" y="59" width="12" height="4"/><rect x="34" y="0" width="4" height="9"/><rect x="6" y="28" width="9" height="4"/><rect x="57" y="28" width="9" height="4"/><path d="M13,10 l3,-3 l7,7 l-3,3 z M59,10 l-3,-3 l-7,7 l3,3 z"/></svg>
      <span class="service-label">Software Tricks, Tips and Tutorials</span>
    </li>
    <li class="service">
      <svg viewBox="0 0 72 72"><path d="M4,8 h40 v26 h-40 z M8,12 l16,12 l16,-12 z"/><path d="M46,30 a16,16 0 1 0 6,24 l-3,-3 a12,12 0 1 1 -3,-21 z M46,36 a6,6 0 1 0 0.1,0 z M52,38 v12 a4,4 0 0 0 8,0 v-6 a16,16 0 0 0 -2,-8 l-3,2 a12,12 0 0 1 1,6 v6 h-1 v-12 z"/></svg>
      <span class="service-label">Internet and Email Setup</span>
    </li>
    <li class="service">
      <svg viewBox="0 0 72 72"><path d="M18,50 a12,12 0 0 1 0,-24 a16,16 0 0 1 30,-6 a14,14 0 0 1 8,28 h-4 v-5 a9,9 0 0 0 -2,-18 a11,11 0 0 0 -21,3 a8,8 0 0 0 -11,17 z"/><path d="M28,38 l-10,7 l10,7 v-4 h14 v-6 h-14 z M46,52 l10,7 l-10,7 v-4 h-14 v-6 h14 z"/></svg>
      <span class="service-label">Data Backup and Recovery</span>
    </li>
    <li class="service">
      <svg viewBox="0 0 72 72"><circle cx="36" cy="26" r="14"/><path d="M18,28 a18,18 0 0 1 36,0 h-4 a14,14 0 0 0 -28,0 z"/><rect x="14" y="24" width="7" height="12" rx="3"/><rect x="51" y="24" width="7" height="12" rx="3"/><path d="M54,36 q0,8 -12,9 v-3 q9,-1 9,-6 z"/><path d="M12,68 a24,20 0 0 1 48,0 z"/></svg>
      <span class="service-label">Onsite and Remote Support Available</span>
    </li>
  </ul>

  <div class="rule rule-top"></div>
  <div class="pricing">
    <p>$40 Per Hour Specific Job, Or Am Happy To Bundle, Provide Flexible Pricing For More Complex Tasks</p>
    <p>No Call Out Fee</p>
    <p>Friendly, Hassle Free, Independent Advice And Recommendations Given</p>
  </div>
  <div class="rule rule-bottom"></div>
</main>
</body>
</html>
```